Oriel Photography Business Card

I need a business card designed for a photography business based in Perth, Western Australia called Oriel Photography.

We specialise in wedding, event photography and portrait photography.

The business card must borrow the style of the attached logo.

The hex codes for the colours in the logo are:
#ED1D85 - Pink
#89C23E - Green
#37282F - Black

The name on the card will be:
Name: Tobrian
Phone: 0417395268
Website: www.orielphotography.example.com.au
Facebook: orielphotography

I am open and happy to accept creative concepts.

I’d like some space at the back for writing notes and appointment details.

```html
<!DOCTYPE html>
<html lang="en">
<head>
<meta charset="utf-8">
<title>Oriel Photography Business Card</title>
<link rel="stylesheet" href="https://fonts.googleapis.com/css2?family=Open+Sans:wght@400;600;700&family=Raleway:wght@400&display=swap">
<style>
  :root {
    --pink: #ED1D85;
    --green: #89C23E;
    --plum: #37282F;
    --plum-soft: #4a3840;
    --paper: #ffffff;
    --ink: #2e2529;
    --rule: #b9b4b6;
    --backdrop: #e4e4ea;
  }
  * { margin: 0; padding: 0; box-sizing: border-box; }
  html, body { width: 1200px; height: 987px; overflow: hidden; }
  body { background: var(--backdrop); font-family: "Open Sans", Arial, sans-serif; position: relative; }

  .card {
    position: absolute; left: 220px; width: 760px; height: 434px;
    border-radius: 26px; overflow: hidden;
    box-shadow: 0 6px 18px rgba(0,0,0,0.15);
  }
  .card--front { top: 36px; background: var(--paper); }
  .card--back { top: 517px; background: var(--plum-soft); }

  .front-wave { position: absolute; inset: 0; }
  .holder-name {
    position: absolute; left: 46px; bottom: 48px;
    color: var(--paper); font-weight: 700; font-size: 26px; letter-spacing: 1px;
  }

  .brand { display: flex; align-items: center; gap: 16px; }
  .brand-mark { width: 46px; height: 46px; border-radius: 50%; background: var(--pink); flex: none; }
  .brand-name {
    font-family: "Raleway", Arial, sans-serif; font-weight: 400;
    font-size: 22px; letter-spacing: 11px; text-transform: uppercase; color: var(--ink);
  }
  .card--front .brand { position: absolute; left: 250px; top: 70px; }

  .contact-list { position: absolute; left: 300px; top: 160px; list-style: none; }
  .contact-list li {
    display: flex; align-items: center; gap: 10px;
    font-size: 20px; color: var(--ink); line-height: 34px;
  }
  .contact-icon { width: 18px; height: 18px; flex: none; }

  .notes-box {
    position: absolute; left: 38px; top: 38px; width: 470px; height: 300px;
    background: var(--paper); padding: 18px 26px;
  }
  .notes-label { font-size: 20px; color: #111; font-weight: 400; }
  .notes-lines { margin-top: 6px; }
  .notes-lines span { display: block; height: 38px; border-bottom: 1px solid var(--rule); }

  .card--back .brand { position: absolute; left: 536px; top: 64px; flex-direction: column; gap: 14px; }
  .card--back .brand-mark { background: var(--paper); width: 54px; height: 54px; }
  .card--back .brand-name { color: var(--paper); font-size: 15px; letter-spacing: 7px; text-align: center; line-height: 26px; }

  .back-web {
    position: absolute; left: 38px; top: 358px; width: 470px;
    text-align: center; color: var(--paper); font-size: 19px; letter-spacing: 1px;
  }
</style>
</head>
<body>
  <section class="card card--front" aria-label="Card front">
    <svg class="front-wave" viewBox="0 0 760 434" aria-hidden="true">
      <path d="M0,236 C210,240 350,360 620,434 L0,434 Z" fill="#ffffff"/>
      <path d="M0,214 C230,220 370,350 660,434 L610,434 C360,362 220,246 0,242 Z" fill="var(--green)"/>
      <path d="M0,256 C200,262 330,370 560,434 L0,434 Z" fill="var(--plum-soft)"/>
    </svg>
    <div class="brand">
      <span class="brand-mark"></span>
      <span class="brand-name">Oriel Photography</span>
    </div>
    <ul class="contact-list">
      <li>
        <svg class="contact-icon" viewBox="0 0 18 18" aria-hidden="true">
          <circle cx="9" cy="9" r="9" fill="var(--green)"/>
          <path d="M6 4.5 L7.6 4.5 L8.3 7 L7.2 7.9 C7.7 9.2 8.8 10.3 10.1 10.8 L11 9.7 L13.5 10.4 L13.5 12 C13.5 12.8 12.8 13.5 12 13.4 C8.2 13 5 9.8 4.6 6 C4.5 5.2 5.2 4.5 6 4.5 Z" fill="#fff"/>
        </svg>
        0417395268
      </li>
      <li><span class="contact-icon" style="background:var(--plum-soft);border-radius:3px"></span>orielphotography</li>
      <li>
        <svg class="contact-icon" viewBox="0 0 18 18" aria-hidden="true">
          <circle cx="9" cy="9" r="8" fill="none" stroke="var(--green)" stroke-width="1.6"/>
          <ellipse cx="9" cy="9" rx="3.5" ry="8" fill="none" stroke="var(--green)" stroke-width="1.2"/>
          <line x1="1" y1="9" x2="17" y2="9" stroke="var(--green)" stroke-width="1.2"/>
        </svg>
        www.orielphotography.example.com.au
      </li>
    </ul>
    <div class="holder-name">TOBRIAN</div>
  </section>

  <section class="card card--back" aria-label="Card back">
    <div class="notes-box">
      <p class="notes-label">notes:</p>
      <div class="notes-lines"><span></span><span></span><span></span><span></span><span></span><span></span></div>
    </div>
    <div class="brand">
      <span class="brand-mark"></span>
      <span class="brand-name">Oriel<br>Photography</span>
    </div>
    <p class="back-web">www.orielphotography.example.com.au</p>
  </section>
</body>
</html>
```